Hollow Thicket, a 3d voxel survival video game needs a card for gaming conventions

I am the lead developer for Hollow Thicket http://www.HollowThicket.example and need a business card to hand out at an indie gaming convention
The card would need to include the game name, website url, my name, position (Lead Developer), e-mail and phone number
The game is a 3d, voxel (with smooth terrain) based survival game with guns and wildlife. The main icon of the game would likely be a grizzly bear but I am willing to accept other designs too.
Attached is a media kit for the game with some images you can use but don't have to its just what little art I can provide. Anything on the website or from the video game can also be used. unrelated art can also be used.
Target Market(s)
Indie Developers/publishers at conferences
Industry/Entity Type
Games
Contact Information for Business Card
Name: Corin Waldrick
Position: Lead Developer
E-mail: Pale_Kettle@mailbox.example
Phone number: 555-372-1186

```html
<!DOCTYPE html>
<html lang="en">
<head>
<meta charset="utf-8">
<title>Hollow Thicket – Business Card</title>
<link rel="stylesheet" href="https://fonts.googleapis.com/css2?family=Open+Sans:wght@400;600;700&display=swap">
<style>
  :root {
    --backdrop: #2b2b2b;
    --card: #141414;
    --accent: #c2461f;
    --text-light: #f2f2f2;
    --text-muted: #b9b9b9;
    --fur-light: #a47048;
    --fur-dark: #5a3920;
    --rock: #d9d6d0;
  }
  * { margin: 0; padding: 0; box-sizing: border-box; }
  html, body {
    width: 1200px; height: 900px; overflow: hidden;
    background: var(--backdrop);
    font-family: "Open Sans", Arial, sans-serif;
  }
  .canvas { position: relative; width: 1200px; height: 900px; }
  .card {
    position: absolute; top: 307px;
    width: 500px; height: 286px;
    border-radius: 20px;
    background: var(--card);
    box-shadow: 0 10px 30px rgba(0,0,0,.45);
    overflow: hidden;
  }
  .card--front { left: 80px; }
  .card--back {
    left: 620px;
    display: flex; flex-direction: column; align-items: center; justify-content: center;
    gap: 12px;
  }

  .mascot-art {
    position: absolute; left: 26px; top: 34px;
    width: 240px; height: 252px;
    border-radius: 46% 40% 0 0 / 30% 30% 0 0;
    background: linear-gradient(180deg, var(--fur-light) 0%, var(--fur-dark) 70%, var(--rock) 86%, var(--rock) 100%);
  }

  .contact {
    position: absolute; left: 292px; top: 96px;
    color: var(--text-light);
  }
  .contact__name {
    color: var(--accent); font-weight: 600; font-size: 17px; line-height: 1.2;
  }
  .contact__role {
    font-size: 13px; line-height: 1.3; margin-bottom: 22px;
  }
  .contact__line {
    display: flex; align-items: center; gap: 8px;
    font-size: 13px; line-height: 1.45;
    white-space: nowrap;
  }
  .contact__icon { width: 11px; height: 11px; flex: none; }

  .brand-name {
    color: var(--accent);
    font-weight: 700; font-size: 30px;
    letter-spacing: 4px; text-transform: uppercase;
  }
  .brand-url {
    color: var(--text-muted);
    font-size: 13px; letter-spacing: .5px;
  }
</style>
</head>
<body>
<main class="canvas">
  <section class="card card--front">
    <div class="mascot-art" role="img" aria-label="Photograph of a grizzly bear standing on a pale rock"></div>
    <div class="contact">
      <p class="contact__name">Corin Waldrick</p>
      <p class="contact__role">Lead Developer</p>
      <p class="contact__line">
        <svg class="contact__icon" viewBox="0 0 24 24" aria-hidden="true"><path fill="#c2461f" d="M6.6 10.8c1.4 2.8 3.8 5.2 6.6 6.6l2.2-2.2c.3-.3.7-.4 1-.2 1.1.4 2.3.6 3.6.6.6 0 1 .4 1 1V20c0 .6-.4 1-1 1C10.6 21 3 13.4 3 4c0-.6.4-1 1-1h3.5c.6 0 1 .4 1 1 0 1.3.2 2.5.6 3.6.1.3 0 .7-.2 1z"/></svg>
        555-372-1186
      </p>
      <p class="contact__line">
        <svg class="contact__icon" viewBox="0 0 24 24" aria-hidden="true"><rect x="2" y="5" width="20" height="14" rx="1" fill="#c2461f"/><path d="M2 6l10 7 10-7" fill="none" stroke="#141414" stroke-width="2"/></svg>
        Pale_Kettle@mailbox.example
      </p>
    </div>
  </section>

  <section class="card card--back">
    <p class="brand-name">Hollow Thicket</p>
    <p class="brand-url">http://www.HollowThicket.example</p>
  </section>
</main>
</body>
</html>
```